New Business Card Design Project LORVANTI-Italy

we are LORVANTI-Italy
our company in the market for 3 years we are luxury cosmetic company and its about time for a facelift :)
i will like to have elegant luxurious and unique business card
that will give the person that get it a unique, luxurious and elegant impression
I'm VERY OPEN FOR NEW IDEAS , even duo i add a few files of things that i see on line and i like them

i add my logo as well
my website is LORVANTI.COM
(if you would like to see the main style that we have)

Target Market(s)

adult that have money :)

Industry/Entity Type

Business

Contact Information for Business Card

Name - Dario Lorvanti
Position - CEO and CO Founder
address - 4817 E Halvern
telephone - 555-384-1926
email - dario@lorvanti.com
fax - 555-384-1926
website - LORVANTI.COM

Colors
000000
959595
fbee3e
ffffff

Requirements
Must have
• big logo in GOLD color
• elegant look
• impressive
Nice to have
• not must but maybe classy pattern background
• not must but maybe emblem
• maybe clear plastic business card
Should not have
• colors
• images

```html
<!DOCTYPE html>
<html lang="en">
<head>
<meta charset="utf-8">
<title>LORVANTI Italy – Business Card</title>
<link rel="stylesheet" href="https://fonts.googleapis.com/css2?family=Cinzel:wght@400;600&family=Lato:wght@400&display=swap">
<style>
  :root {
    --page: #ffffff;
    --card-dark: #0e0e0e;
    --gold: #e9bd3c;
    --gold-soft: #f3d06a;
    --gold-deep: #d9b447;
    --ink-light: #ffffff;
    --icon-ink: #0e0e0e;
  }
  * { margin: 0; padding: 0; box-sizing: border-box; }
  html, body { width: 1200px; height: 900px; overflow: hidden; background: var(--page); }
  .canvas { position: relative; width: 1200px; height: 900px; }

  .card { position: absolute; top: 184px; height: 490px; border-radius: 14px; }
  .card-front { left: 299px; width: 301px; background: var(--card-dark); }
  .card-back { left: 645px; width: 305px; background: var(--gold-soft); overflow: hidden; }

  .brand { position: absolute; left: 0; right: 0; top: 40px; text-align: center; }
  .brand-dot { display: block; width: 92px; height: 92px; margin: 0 auto; border-radius: 50%; border: 3px solid var(--gold); }
  .brand-name {
    margin-top: 18px; font-family: "Cinzel", serif; font-weight: 400;
    font-size: 38px; line-height: 1; color: var(--gold); letter-spacing: 0.5px;
  }
  .brand-place {
    margin-top: 14px; font-family: "Cinzel", serif; font-weight: 400;
    font-size: 15px; color: var(--gold); letter-spacing: 1px;
  }

  .person { position: absolute; left: 31px; top: 292px; }
  .person-name { font-family: "Cinzel", serif; font-weight: 600; font-size: 21px; color: var(--gold); letter-spacing: 0.3px; }
  .person-role { margin-top: 3px; font-family: "Lato", sans-serif; font-size: 13px; color: var(--ink-light); }

  .contacts { position: absolute; left: 31px; top: 360px; list-style: none; }
  .contacts li {
    display: flex; align-items: center; gap: 6px; height: 22.5px;
    font-family: "Lato", sans-serif; font-size: 13.5px; color: var(--ink-light);
  }
  .contacts svg { width: 16px; height: 16px; flex: none; }

  .back-mark {
    position: absolute; left: 42px; top: 112px; width: 238px; height: 262px;
    display: flex; flex-direction: column; align-items: center; justify-content: center;
  }
  .back-ring { width: 238px; height: 238px; border-radius: 50%; border: 5px solid var(--gold-deep); opacity: 0.8;
    display: flex; align-items: center; justify-content: center; }
  .back-name { font-family: "Cinzel", serif; font-weight: 400; font-size: 34px; color: var(--gold-deep); }
</style>
</head>
<body>
<main class="canvas">
  <section class="card card-front" aria-label="Business card front">
    <header class="brand">
      <span class="brand-dot"></span>
      <p class="brand-name">LORVANTI</p>
      <p class="brand-place">ITALY</p>
    </header>

    <div class="person">
      <h1 class="person-name">DARIO LORVANTI</h1>
      <p class="person-role">CEO and CO Founder</p>
    </div>

    <ul class="contacts">
      <li>
        <svg viewBox="0 0 16 16" aria-hidden="true"><circle cx="8" cy="8" r="8" fill="var(--gold-soft)"/>
          <path d="M4 7.5c0-2 8-2 8 0v1h-2v-1H6v1H4z M5 9.5h6l.5 2.5h-7z" fill="var(--icon-ink)"/></svg>
        555-384-1926
      </li>
      <li>
        <svg viewBox="0 0 16 16" aria-hidden="true"><circle cx="8" cy="8" r="8" fill="var(--gold-soft)"/>
          <rect x="5.5" y="4" width="5" height="3" fill="var(--icon-ink)"/><rect x="4.5" y="7" width="7" height="5" rx="1" fill="var(--icon-ink)"/></svg>
        555-384-1926
      </li>
      <li>
        <svg viewBox="0 0 16 16" aria-hidden="true"><circle cx="8" cy="8" r="8" fill="var(--gold-soft)"/>
          <rect x="4" y="5" width="8" height="6" fill="var(--icon-ink)"/><path d="M4 5l4 3.2L12 5" stroke="var(--gold-soft)" fill="none"/></svg>
        dario@lorvanti.com
      </li>
      <li>
        <svg viewBox="0 0 16 16" aria-hidden="true"><circle cx="8" cy="8" r="8" fill="var(--gold-soft)"/>
          <circle cx="8" cy="8" r="4" fill="none" stroke="var(--icon-ink)" stroke-width="1.6"/><path d="M4 8h8M8 4v8" stroke="var(--icon-ink)" stroke-width="1"/></svg>
        LORVANTI.COM
      </li>
    </ul>
  </section>

  <section class="card card-back" aria-label="Business card back">
    <div class="back-mark">
      <div class="back-ring"><p class="back-name">LORVANTI</p></div>
    </div>
  </section>
</main>
</body>
</html>
```